Logo, Web and Mobile Designs for enterprise social media platform

All the details are in the attached document, please start reading the scope document first which explains what is this project about and the details about the needed deliverables, after that please read the UI_Requirements document which will detail what is expected regarding the coded web version since this is a coded contest, it is very important that you meet the UI requirements or suggest something else but we will need to agree first before working on the coded version

Good Luck

Target Market(s)

Enterprise Social Media

Industry/Entity Type

Media

Coding

Coded - Design and coding required

Number of Pages Required

5+ page

Font styles to use
Sans Serif

Requirements
Must have
• All the must haves are listed in the scope document so please check before you start

```html
<!DOCTYPE html>
<html lang="en">
<head>
<meta charset="utf-8">
<title>Teamora – Business Opportunity Network</title>
<link href="https://fonts.googleapis.com/css2?family=Roboto:wght@400;500;700&family=Open+Sans:ital,wght@0,400;1,400&display=swap" rel="stylesheet">
<style>
:root{
  --page:#eeeeee;
  --panel:#ffffff;
  --panel-head:#f7f7f7;
  --line:#e3e3e3;
  --field-line:#dcdcdc;
  --text:#444444;
  --muted:#777777;
  --orange:#ef9400;
  --blue:#1f8fcb;
  --blue-link:#2a9ad6;
  --footer:#2a8bc0;
  --photo:#8d8b86;
}
*{box-sizing:border-box;margin:0;padding:0}
html,body{width:770px;height:1200px;overflow:hidden}
body{position:relative;background:var(--page);font-family:'Roboto',sans-serif;color:var(--text)}
.abs{position:absolute}
.topbar{position:absolute;left:0;top:0;width:770px;height:46px;background:#fff;border-bottom:1px solid #dedede}
.brand{position:absolute;left:108px;top:10px;display:flex;align-items:center;gap:6px}
.brand-dot{width:26px;height:26px;border-radius:50%;background:var(--orange)}
.brand-name{font-size:20px;font-weight:500;color:var(--blue)}
.user{position:absolute;left:478px;top:12px;display:flex;align-items:center;gap:7px;font-size:11.5px;color:#555}
.avatar{width:22px;height:22px;border-radius:50%;background:#5a5752}
.sep{position:absolute;top:0;width:1px;height:46px;background:#ececec}
.badge{position:absolute;width:12px;height:11px;border-radius:6px;font-size:7px;color:#fff;text-align:center;line-height:11px}
.panel{position:absolute;left:63px;width:642px;background:var(--panel);border:1px solid #e0e0e0}
.panel-head{height:31px;background:var(--panel-head);border-bottom:1px solid var(--line);padding:0 12px;font-size:10px;line-height:31px;color:#444;letter-spacing:.1px}
.label{position:absolute;font-size:9.5px;color:#555}
.field{position:absolute;background:#fff;border:1px solid var(--field-line)}
.btn{position:absolute;color:#fff;font-size:9.5px;text-align:center;border-radius:2px}
.btn-orange{background:var(--orange);font-weight:500;font-size:10px}
.btn-blue{background:var(--blue);font-size:8px}
.group-row{position:absolute;left:0;width:640px;border-top:1px solid #f0f0f0}
.group-pic{position:absolute;left:18px;width:44px;height:44px;border-radius:50%}
.group-title{position:absolute;left:74px;font-size:10px;color:var(--blue-link)}
.group-text{position:absolute;left:74px;font-family:'Open Sans',sans-serif;font-style:italic;font-size:6.6px;line-height:12px;color:#555}
.chev{position:absolute;left:626px}
.radio{position:absolute;font-family:'Open Sans',sans-serif;font-size:7.5px;color:#666;display:flex;align-items:center;gap:6px}
.radio i{width:10px;height:10px;border:1px solid #ccc;border-radius:50%;display:inline-block;position:relative}
.radio i.on::after{content:"";position:absolute;left:2.5px;top:2.5px;width:3px;height:3px;border-radius:50%;background:#aaa}
.acc{position:absolute;left:120px;width:302px;font-family:'Open Sans',sans-serif;font-size:7.5px;color:#444}
.acc-head{height:24px;line-height:24px;padding-left:10px;background:#f7f7f7;border:1px solid #ececec;position:relative}
.acc-toggle{position:absolute;right:0;top:-1px;width:22px;height:24px;text-align:center;font-size:13px;line-height:22px;color:var(--orange)}
.acc-toggle.open{background:var(--orange);color:#fff}
.acc-body{border:1px solid #ececec;border-top:0;padding:11px 16px;font-size:6.8px;line-height:13px;height:65px;color:#444}
.footer{position:absolute;left:0;top:1106px;width:770px;height:94px;background:var(--footer);color:#fff;text-align:center}
.social{display:flex;justify-content:center;gap:8px;margin-top:17px}
.social span{width:16px;height:16px;background:#fff;border-radius:3px}
.footer-links{margin-top:14px;font-size:9px;color:#e8f3fa}
.footer-links b{font-weight:400;margin:0 5px}
.copyright{margin-top:9px;font-size:8.6px}
</style>
</head>
<body>

<header class="topbar">
  <svg class="abs" style="left:64px;top:18px" width="12" height="10"><rect y="0" width="12" height="2" fill="#888"/><rect y="4" width="12" height="2" fill="#888"/><rect y="8" width="12" height="2" fill="#888"/></svg>
  <div class="sep" style="left:92px"></div>
  <div class="brand"><span class="brand-dot"></span><span class="brand-name">Teamora</span></div>
  <div class="user"><span class="avatar" role="img" aria-label="User profile photo"></span>Daniel Reyes
    <svg width="8" height="5"><path d="M0 0h8L4 5z" fill="#555"/></svg></div>
  <div class="sep" style="left:592px"></div>
  <svg class="abs" style="left:606px;top:17px" width="13" height="12"><rect width="7" height="3" fill="#666"/><rect y="4.5" width="13" height="3" fill="#666"/><rect y="9" width="9" height="3" fill="#666"/></svg>
  <span class="badge" style="left:614px;top:10px;background:var(--orange)">8</span>
  <div class="sep" style="left:636px"></div>
  <svg class="abs" style="left:648px;top:17px" width="13" height="13"><circle cx="5.5" cy="5.5" r="4.3" fill="none" stroke="#666" stroke-width="1.8"/><path d="M8.5 8.5l3.5 3.5" stroke="#666" stroke-width="2"/></svg>
  <div class="sep" style="left:676px"></div>
  <svg class="abs" style="left:688px;top:17px" width="12" height="13"><path d="M6 0.5a4 4 0 0 1 4 4v4l1.5 2H0.5L2 8.5v-4a4 4 0 0 1 4-4z" fill="#666"/><circle cx="6" cy="11.8" r="1.3" fill="#666"/></svg>
  <span class="badge" style="left:693px;top:10px;background:var(--blue)">8</span>
</header>

<section class="panel" style="top:72px;height:249px">
  <div class="panel-head">BUSINESS OPPORTUNITY NETWORK
    <svg class="abs" style="right:18px;top:12px" width="5" height="8"><path d="M1 1l3 3-3 3" fill="none" stroke="#aaa"/></svg></div>
  <span class="label" style="left:24px;top:56px">Name : *</span>
  <div class="field" style="left:118px;top:50px;width:300px;height:25px"></div>
  <span class="label" style="left:24px;top:89px">About : *</span>
  <div class="field" style="left:118px;top:83px;width:300px;height:25px"></div>
  <span class="label" style="left:24px;top:124px">Description : *</span>
  <div class="field" style="left:118px;top:118px;width:300px;height:80px"></div>
  <div class="btn btn-orange" style="left:118px;top:210px;width:73px;height:21px;line-height:21px">UPDATE</div>
</section>

<section class="panel" style="top:336px;height:282px">
  <div class="panel-head">GROUPS NAME</div>
  <div class="btn btn-blue" style="left:562px;top:5px;width:72px;height:21px;line-height:21px">ADD MORE ✚</div>
  <div class="field" style="left:14px;top:45px;width:246px;height:21px;font-family:'Open Sans',sans-serif;font-size:6.8px;color:#777;padding:6px 10px">add a new group name</div>
  <div class="btn btn-blue" style="left:267px;top:45px;width:91px;height:21px;line-height:21px">✚ ADD NEW GROUP</div>

  <div class="group-row" style="top:81px;height:66px">
    <div class="group-pic" role="img" aria-label="Photo of a businessman" style="top:10px;background:#6b6660"></div>
    <span class="group-title" style="top:13px">Administrators</span>
    <p class="group-text" style="top:28px">Lorem ipsum dolor sit amet,<br>consectetur adipiscing elit, sed do</p>
    <svg class="chev" style="top:30px" width="8" height="8"><path d="M1 4l3-3 3 3M1 7l3-3 3 3" fill="none" stroke="#555"/></svg>
  </div>
  <div class="group-row" style="top:147px;height:67px">
    <div class="group-pic" role="img" aria-label="Photo of buyers viewing a house" style="top:11px;background:var(--photo)"></div>
    <span class="group-title" style="top:13px">Buyers</span>
    <p class="group-text" style="top:28px">Lorem ipsum dolor sit amet,<br>consectetur adipiscing elit, sed do</p>
    <svg class="chev" style="top:31px" width="8" height="8"><path d="M1 4l3-3 3 3M1 7l3-3 3 3" fill="none" stroke="#555"/></svg>
  </div>
  <div class="group-row" style="top:214px;height:67px">
    <div class="group-pic" role="img" aria-label="Photo of sellers meeting in an office" style="top:10px;background:#a09d98"></div>
    <span class="group-title" style="top:11px">Sellers</span>
    <p class="group-text" style="top:26px">Lorem ipsum dolor sit amet,<br>consectetur adipiscing elit, sed do</p>
    <svg class="chev" style="top:30px" width="8" height="8"><path d="M1 4l3-3 3 3M1 7l3-3 3 3" fill="none" stroke="#555"/></svg>
  </div>
</section>

<section class="panel" style="top:638px;height:442px">
  <div class="panel-head">BUSINESS OPPORTUNITY ITEMS</div>
  <span class="label" style="left:27px;top:60px">Name : *</span>
  <div class="field" style="left:120px;top:53px;width:300px;height:25px"></div>
  <span class="label" style="left:27px;top:92px">Description : *</span>
  <div class="field" style="left:120px;top:87px;width:300px;height:80px"></div>
  <div class="field" style="left:120px;top:176px;width:215px;height:25px"></div>
  <div class="btn" style="left:334px;top:176px;width:86px;height:25px;line-height:25px;background:var(--blue-link);font-size:9px">UPLOADED</div>
  <span class="radio" style="left:120px;top:221px"><i></i>Public</span>
  <span class="radio" style="left:179px;top:221px"><i class="on"></i>Private</span>
  <div class="btn btn-orange" style="left:120px;top:236px;width:73px;height:21px;line-height:21px">ADD</div>

  <div class="acc" style="top:276px">
    <div class="acc-head">Cedar Ridge 6th of October<span class="acc-toggle open">–</span></div>
    <div class="acc-body">Lorem ipsum dolor sit amet, consectetur adipiscing elit, sed do eiusmod tempor incididunt ut labore et dolore magna aliqua. Ut enim ad minim veniam, quis nostrud exercitation ullamco laboris nisi ut aliquip</div>
  </div>
  <div class="acc" style="top:369px"><div class="acc-head">Cedar Ridge New Cairo<span class="acc-toggle">+</span></div></div>
  <div class="acc" style="top:396px"><div class="acc-head">Cedar Ridge North Coast<span class="acc-toggle">+</span></div></div>
</section>

<footer class="footer">
  <div class="social"><span></span><span></span><span></span><span></span><span></span></div>
  <div class="footer-links">Home<b>/</b>Contact<b>/</b>Topics<b>/</b>Posts and Comments<b>/</b>Discussion<b>/</b>Videos Links</div>
  <div class="copyright">Copyright @ 2015 - 2015.Teamora. All Rights Reserved.</div>
</footer>

</body>
</html>
```